Laser Tattoo Removal Business Cards

We are looking for a professional business card design for a laser tattoo removal business. Ideally looking for a black business card design. The name of the business is Brightline Tattoo Removal. We place our cards at local tattoo shops so we ideally are looking for something trendy/edgy to draw both male and female clientele in.

Target Market(s)

Male/Female ages 18-60

Contact Information for Business Card

black background ideally.. hoping to stay within greys, whites and black

Font styles to use
Serif
Sans Serif

Colors
121212
a9a9a9
5c5c5c
f5f5f5
ffffff
7f7f7f
606060
848484
9d9d9d

Requirements
Must have
• Employee Info:
• Melissa Thornbury
• Chief Executive Offer
• m: 919.537.2846
• w: 919.362.4178
• f: 919.685.3907
• mthornbury@brightlinetattooremoval.example
• Address:
• 4615 Oakmere Pkwy, Suite 210
• Raleigh, NC 27654
• Website:
• www.brightlinetattooremoval.example
Nice to have
• Myabe business name on back or logo on back and employee info on the front

```html
<!DOCTYPE html>
<html lang="en">
<head>
<meta charset="utf-8">
<title>Brightline Tattoo Removal — Business Card</title>
<link rel="stylesheet" href="https://fonts.googleapis.com/css2?family=Roboto+Condensed:wght@700&family=Roboto:wght@400;500&display=swap">
<style>
  :root {
    --backdrop: #2b2b2b;
    --card: #121212;
    --ink: #ffffff;
    --ink-soft: #f5f5f5;
    --rule: #a9a9a9;
  }
  html, body {
    margin: 0;
    padding: 0;
    width: 1200px;
    height: 900px;
    overflow: hidden;
    background: var(--backdrop);
  }
  .canvas {
    position: relative;
    width: 1200px;
    height: 900px;
  }
  .card {
    position: absolute;
    left: 230px;
    width: 740px;
    height: 410px;
    background: var(--card);
    color: var(--ink);
    box-shadow: 0 6px 18px rgba(0,0,0,0.45);
  }
  .card--front { top: 28px; }
  .card--back { top: 462px; }

  /* Front */
  .brand-name {
    position: absolute;
    top: 150px;
    left: 0;
    width: 100%;
    text-align: center;
    font-family: "Roboto Condensed", "Arial Narrow", sans-serif;
    font-weight: 700;
    font-size: 44px;
    letter-spacing: 4px;
    color: var(--ink);
    margin: 0;
  }
  .brand-site {
    position: absolute;
    top: 262px;
    left: 0;
    width: 100%;
    text-align: center;
    font-family: "Roboto", Arial, sans-serif;
    font-size: 17px;
    letter-spacing: 3.5px;
    color: var(--ink-soft);
  }

  /* Back */
  .person {
    position: absolute;
    top: 152px;
    right: 432px;
    text-align: right;
  }
  .person-name {
    margin: 0;
    font-family: "Roboto Condensed", "Arial Narrow", sans-serif;
    font-weight: 700;
    font-size: 33px;
    line-height: 1;
    color: var(--ink);
  }
  .person-title {
    margin: 4px 0 0;
    font-family: "Roboto", Arial, sans-serif;
    font-weight: 500;
    font-size: 18px;
    color: var(--ink-soft);
  }
  .divider {
    position: absolute;
    left: 324px;
    top: 128px;
    width: 1px;
    height: 120px;
    background: var(--rule);
  }
  .contact-list {
    position: absolute;
    left: 342px;
    top: 136px;
    margin: 0;
    padding: 0;
    list-style: none;
    font-family: "Roboto", Arial, sans-serif;
    font-size: 15px;
    color: var(--ink-soft);
  }
  .contact-list li {
    display: flex;
    align-items: center;
    height: 21px;
  }
  .contact-icon {
    width: 14px;
    height: 14px;
    margin-right: 9px;
    fill: var(--ink);
    flex: none;
  }
  .address {
    position: absolute;
    left: 48px;
    top: 336px;
    display: flex;
    align-items: center;
    font-family: "Roboto", Arial, sans-serif;
    font-size: 19px;
    color: var(--ink-soft);
  }
  .address .contact-icon {
    width: 16px;
    height: 20px;
    margin-right: 6px;
  }
</style>
</head>
<body>
<main class="canvas">

  <section class="card card--front" aria-label="Card front">
    <h1 class="brand-name">BRIGHTLINE TATTOO REMOVAL</h1>
    <div class="brand-site">www.brightlinetattooremoval.example</div>
  </section>

  <section class="card card--back" aria-label="Card back">
    <div class="person">
      <h2 class="person-name">MELISSA THORNBURY</h2>
      <p class="person-title">Chief Executive Offer</p>
    </div>

    <div class="divider"></div>

    <ul class="contact-list">
      <li>
        <svg class="contact-icon" viewBox="0 0 16 16" aria-hidden="true"><path d="M3.5 1 6 1.5 7 5 5.3 6.4a9 9 0 0 0 4.3 4.3L11 9l3.5 1 .5 2.5-1.8 1.8C6.8 14.6 1.4 9.2 1.7 2.8Z"/></svg>
        919.362.4178
      </li>
      <li>
        <svg class="contact-icon" viewBox="0 0 16 16" aria-hidden="true"><path d="M4 0h8a1 1 0 0 1 1 1v14a1 1 0 0 1-1 1H4a1 1 0 0 1-1-1V1a1 1 0 0 1 1-1Zm1 2v10h6V2Zm3 11a1 1 0 1 0 0 2 1 1 0 0 0 0-2Z" fill-rule="evenodd"/></svg>
        919.537.2846
      </li>
      <li>
        <svg class="contact-icon" viewBox="0 0 16 16" aria-hidden="true"><path d="M4 1h7l1 1v3H4Zm-3 5h14v7h-3v2H4v-2H1Zm4 5v3h6v-3Z" fill-rule="evenodd"/></svg>
        919.685.3907
      </li>
      <li>
        <svg class="contact-icon" viewBox="0 0 16 16" aria-hidden="true"><path d="M1 3h14v1L8 9 1 4Zm0 2.5 7 5 7-5V13H1Z"/></svg>
        mthornbury@brightlinetattooremoval.example
      </li>
      <li>
        <svg class="contact-icon" viewBox="0 0 16 16" aria-hidden="true"><circle cx="8" cy="8" r="7"/></svg>
        www.brightlinetattooremoval.example
      </li>
    </ul>

    <div class="address">
      <svg class="contact-icon" viewBox="0 0 16 20" aria-hidden="true"><path d="M8 0a7 7 0 0 0-7 7c0 5 7 13 7 13s7-8 7-13a7 7 0 0 0-7-7Zm0 4a3 3 0 1 1 0 6 3 3 0 0 1 0-6Z" fill-rule="evenodd"/></svg>
      4615 Oakmere Pkwy, Suite 210, Raleigh, NC 27654
    </div>
  </section>

</main>
</body>
</html>
```